Join Wait / Reservations Handout

This is a handout for guests with information about the ability to join our
waitlist and/or make reservations. It will be handed out to any guest that ends up waiting on our waitlist to be seated. It will describe how our waitlist and reservations system works. It is informational for them to download our mobile app.

It was forcing me to move the look and feel sliders. Please refer to our branding guide for look and feel.

Industry/Entity Type

Hospitality

Contact Information for Business Card

One of the attached documents give a very generic layout of the information we need on this card. This layout is more for where we wanted the information placed and has nothing to do with the design aspects of the piece. Please use your imagination. Any of the 5 colors in the branding guide can be used anywhere. The pineapple design can be used anywhere in any color combination.

If you require any other files please let me know. Thanks

Other font styles liked:
• Please see attached branding guide

Requirements
Must have
• The only color requirement is that the logo be the blue with teal lettering...This has to match our app store logo.

```html
<!DOCTYPE html>
<html lang="en">
<head>
<meta charset="utf-8">
<title>Join the Wait – Guest Handout</title>
<link rel="stylesheet" href="https://fonts.googleapis.com/css2?family=League+Spartan:wght@700;800&family=Josefin+Sans:ital,wght@0,300;0,400;1,300&display=swap">
<style>
  :root {
    --navy: #0f2b46;
    --teal: #5aa8a6;
    --paper: #ffffff;
    --pattern: #eef0f2;
    --backdrop: #e9e9ea;
    --heading: "League Spartan", "Futura", sans-serif;
    --body: "Josefin Sans", "Helvetica Neue", sans-serif;
  }
  * { box-sizing: border-box; margin: 0; padding: 0; }
  html, body { width: 1200px; height: 863px; overflow: hidden; }
  body { background: var(--backdrop); position: relative; font-family: var(--body); }

  .card {
    position: absolute; top: 140px; width: 330px; height: 570px;
    background: var(--paper); box-shadow: 0 6px 22px rgba(0,0,0,.12);
    overflow: hidden;
  }
  .card--info { left: 250px; padding: 40px 0; }
  .card--app { left: 620px; }

  /* Info side */
  .info-block { padding: 0 26px; text-align: right; margin-bottom: 38px; }
  .info-block__title {
    font-family: var(--heading); font-weight: 800; font-size: 15px;
    color: var(--navy); letter-spacing: .3px; text-transform: uppercase;
  }
  .info-block__text { font-weight: 300; font-size: 14px; color: var(--teal); line-height: 1.25; margin-top: 4px; }
  .info-panel { margin: 0 26px 38px; padding: 16px 14px 18px; text-align: left; }
  .info-panel--teal { background: var(--teal); }
  .info-panel--navy { background: var(--navy); margin-top: 26px; }
  .info-panel .info-block__title { color: var(--paper); font-style: italic; font-size: 16px; }
  .info-panel--teal .info-block__text { color: var(--paper); }
  .info-panel--navy .info-block__text { color: var(--teal); }

  /* App side */
  .pattern-field { position: absolute; inset: 0; background: var(--pattern); }
  .app-content { position: relative; padding: 34px 22px 0; }
  .app-headline {
    font-family: var(--heading); font-weight: 800; font-size: 46px; line-height: .9;
    color: var(--navy); text-transform: uppercase; letter-spacing: .5px;
  }
  .app-subline { font-size: 24px; font-weight: 300; color: var(--teal); margin-top: 2px; }
  .rule { background: var(--navy); margin: 0 -4px; }
  .rule--thick { height: 9px; margin-top: 16px; }
  .rule--thin { height: 3px; margin-top: 4px; }
  .rule-group--lower .rule--thick { margin-top: 0; }
  .rule-group--lower { margin-top: 28px; }
  .rule-group--lower .rule--thin { margin-top: 0; margin-bottom: 4px; }
  .brand-box {
    width: 160px; height: 108px; margin: 28px auto 0; background: var(--navy);
    display: flex; align-items: center; justify-content: center; text-align: center;
  }
  .brand-box__name { font-family: var(--body); font-weight: 400; font-size: 21px; color: var(--teal); line-height: 1.2; }
  .search-row { display: flex; align-items: center; justify-content: space-between; margin-top: 12px; }
  .store-mark { width: 24px; height: 24px; background: var(--navy); border-radius: 4px; }
  .search-label {
    font-family: var(--heading); font-weight: 800; font-size: 30px; color: var(--navy);
    letter-spacing: 2px; text-transform: uppercase;
  }
  .search-term {
    margin-top: 8px; background: var(--teal); color: var(--navy);
    font-size: 19px; font-weight: 400; text-align: center; padding: 6px 4px 4px;
  }
</style>
</head>
<body>

<section class="card card--info" aria-label="Waitlist and reservation details">
  <div class="info-block">
    <h2 class="info-block__title">When to join the wait</h2>
    <p class="info-block__text">Anytime</p>
  </div>

  <div class="info-panel info-panel--teal">
    <h2 class="info-block__title">When to reserve</h2>
    <p class="info-block__text">Anytime – 2 hours in advance<br>(excluding weekend, open - 2pm)</p>
  </div>

  <div class="info-block">
    <h2 class="info-block__title">Sunday buffet</h2>
    <p class="info-block__text">Sunday + Holiday Buffets<br>(Coming June 2018)</p>
  </div>

  <div class="info-panel info-panel--navy">
    <h2 class="info-block__title">Large groups</h2>
    <p class="info-block__text">Large Groups handled/contacted<br>by Catering manager</p>
  </div>
</section>

<section class="card card--app" aria-label="Download our app">
  <div class="pattern-field" role="img" aria-label="Faint repeating brand pattern in light grey"></div>
  <div class="app-content">
    <h1 class="app-headline">Save<br>the wait...</h1>
    <p class="app-subline">Download Our App</p>
    <div class="rule rule--thick"></div>
    <div class="rule rule--thin"></div>

    <div class="brand-box">
      <span class="brand-box__name">Harborview<br>Diner</span>
    </div>

    <div class="rule-group--lower">
      <div class="rule rule--thin"></div>
      <div class="rule rule--thick"></div>
    </div>

    <div class="search-row">
      <span class="store-mark" aria-hidden="true"></span>
      <span class="search-label">Search</span>
      <span class="store-mark" aria-hidden="true"></span>
    </div>
    <p class="search-term">“Harborview Diner”</p>
  </div>
</section>

</body>
</html>
```